Executive recruiting firm in need of business card design

Executive recruiting firm looking for a sleek, classy and modern business card design; card itself will be square shape, rounded edges and soft touch paper, our colors are dark blues in the navy color scale, silvers and grays. Reference our website for a better idea of our company's feel and goals at Tarvex-Up.com - our company message is "Employee Engagement Begins at Recruitment" this should be on the card

```html
<!DOCTYPE html>
<html lang="en">
<head>
<meta charset="utf-8">
<title>Tarvex Up — Business Card</title>
<link rel="stylesheet" href="https://fonts.googleapis.com/css2?family=Barlow:wght@300;400;500;700&display=swap">
<style>
  :root {
    --navy: #111543;
    --navy-deep: #0e1240;
    --paper: #f4f4f4;
    --paper-shade: #e6e6e6;
    --ink-grey: #5a5a5a;
    --band-grey: #6b6b6b;
    --backdrop: #e2e2e2;
    --white: #ffffff;
  }
  * { box-sizing: border-box; margin: 0; padding: 0; }
  html, body {
    width: 1200px;
    height: 576px;
    overflow: hidden;
    background: var(--backdrop);
    font-family: "Barlow", sans-serif;
  }
  .stage { position: relative; width: 1200px; height: 576px; }
  .card {
    position: absolute;
    top: 98px;
    width: 380px;
    height: 380px;
    border-radius: 18px;
    overflow: hidden;
    box-shadow: 0 3px 6px rgba(0,0,0,0.18);
  }

  /* Front */
  .card-front { left: 190px; background: var(--navy); }
  .card-front .backdrop-photo {
    position: absolute;
    inset: 0;
    background: linear-gradient(180deg, #131848 0%, var(--navy-deep) 60%, #10143f 100%);
  }
  .brand {
    position: absolute;
    font-family: "Barlow", sans-serif;
    white-space: nowrap;
  }
  .brand .name { display: block; font-weight: 300; }
  .brand .message {
    display: block;
    margin-top: 6px;
    font-size: 9.5px;
    font-weight: 400;
    letter-spacing: 1.6px;
  }
  .card-front .brand {
    left: 0;
    right: 0;
    top: 158px;
    text-align: center;
    color: var(--white);
  }
  .card-front .brand .name { font-size: 38px; letter-spacing: 4px; line-height: 42px; }

  /* Back */
  .card-back {
    left: 630px;
    background: linear-gradient(180deg, var(--paper) 0%, var(--paper-shade) 100%);
  }
  .card-back .brand { left: 40px; top: 56px; color: var(--navy); }
  .card-back .brand .name { font-size: 30px; letter-spacing: 3px; line-height: 34px; }
  .card-back .brand .message { color: var(--ink-grey); font-size: 8.5px; letter-spacing: 1.3px; }

  .contact {
    position: absolute;
    left: 40px;
    top: 156px;
    color: var(--ink-grey);
    font-size: 12px;
    line-height: 16px;
  }
  .contact .person-name { color: var(--navy); font-size: 19px; font-weight: 700; line-height: 22px; }
  .contact .person-role { margin-top: 4px; font-size: 11.5px; }
  .contact .address { margin-top: 18px; }
  .contact .line { display: flex; align-items: center; gap: 12px; margin-top: 4px; }
  .contact .line:first-of-type { margin-top: 8px; }
  .contact .icon { width: 12px; height: 10px; flex: none; fill: var(--navy); }

  .footer-grey {
    position: absolute;
    left: 0;
    bottom: 0;
    width: 200px;
    height: 13px;
    background: var(--band-grey);
  }
  .footer-band {
    position: absolute;
    right: 0;
    bottom: 0;
    width: 200px;
    height: 34px;
    background: var(--navy);
    clip-path: polygon(18px 0, 100% 0, 100% 100%, 0 100%);
  }
  .footer-band .site {
    position: absolute;
    left: 42px;
    top: 9px;
    color: var(--white);
    font-size: 12px;
    font-weight: 500;
  }
</style>
</head>
<body>
<main class="stage">
  <section class="card card-front">
    <div class="backdrop-photo" role="img" aria-label="Dark navy-toned photo of an executive standing at an office window overlooking a city"></div>
    <div class="brand">
      <span class="name">TARVEX UP</span>
      <span class="message">employee engagement begins at recruitment</span>
    </div>
  </section>

  <section class="card card-back">
    <div class="brand">
      <span class="name">TARVEX UP</span>
      <span class="message">employee engagement begins at recruitment</span>
    </div>

    <div class="contact">
      <p class="person-name">Employee Name</p>
      <p class="person-role">Managing Director</p>
      <p class="address">482 W Alder Ave, Brookvale,<br>CA 90210, USA</p>
      <p class="line">
        <svg class="icon" viewBox="0 0 12 10" aria-hidden="true"><path d="M1 3.2C1 1.8 3 1 6 1s5 .8 5 2.2v.8H8.6V2.9H3.4V4H1z"/><path d="M3.3 4.6h5.4L10.5 9h-9z"/></svg>
        <span>00-5678-5678-90</span>
      </p>
      <p class="line">
        <svg class="icon" viewBox="0 0 12 10" aria-hidden="true"><path d="M0 1h12v8H0z"/><path d="M0.6 1.4L6 5.6l5.4-4.2" fill="none" stroke="#f2f2f2" stroke-width="1"/></svg>
        <span>employee@tarvex-up.com</span>
      </p>
    </div>

    <div class="footer-grey"></div>
    <div class="footer-band"><span class="site">www.tarvex-up.com</span></div>
  </section>
</main>
</body>
</html>
```